Redesign company trifold brochure

We are rebranding our company in September and looking for a more professional design for our brochure.

What we do - providing interdisciplinary care for those supporting ill, elderly and special needs pets at home following the human hospice model of care - is very novel and our brochure is key in explaining it and our offerings.

We serve dogs and cats. Most of the animals are quite sick, elderly. I have many personal and stock photos we can use in the brochure. Please - no pictures of puppies and/or kittens.

The hard part is fitting the info and message into a clear and concise format.

It must be appealing both to pet owners and vets (who are our primary source of patients through referrals).

It should covey WARMTH, COMPASSION, PROFESSIONALISM, and EXPERTISE.

Please look at our website www.TrellisAnimalRespite.com for more info

We have until now used maroon and copper for colors - to reflect the "sunset" of the pets life. BUT are now changing to Navy, Teal and White to reflect calm, trust and competence.

We will use the same logo recolored.

Existing brochure and new logo are attached.

PLEASE ask questions!!
Updates

We have a library of stock images you are welcome to use. All have been legally acquired and we have the right to use them. You DO NOT have to use them, just sending along in case you wish to. https://www.filecrate.example/sh/qk4vrm82zd1pyno/KLQ7Ztbn-Rrfx2mh9sWpYJ4Dc?dl=0

Our colors are NAVY, TEAL and WHITE. For your reference, the navy we use is 99/87/44/55 (CMYK) The Teal we use is 76/11/44/0 (CMYK) Thank you!

Designers -- pleaseuse pictures of older pets (no puppies or kittens). Below is a link to stock photos we own that would be appropriate for use in the brochure. https://www.filecrate.example/sh/w274m6t9pxkr5da/KLRn3GsfwlTVBXEPcq_8ZNj5u?dl=0 THANK YOU!

Designers -- I would VERY much like to include a photo of a pet in a wheel chair. I have personal photos as well as (purchased) stock photos for this purpose which can be found at http://lnk.example/TARHC-Pets-in-Wheelchairs Thank you!!

Today is the last day! Many of you have submitted beautiful designs and others are rolling in. I am so appreciative of your time and energy!! Please do not let the deadline pass without YOUR very BEST entry being submitted!! Thank you! - Miriam & All of us at Trellis Animal Respite & Home Care

Target Market(s)

Pet Owners and Veterinarians

Industry/Entity Type

Pet Care

Font styles to use
Serif

Colors
0455a3
33b8a4
ffffff

Requirements
Must have
• Our logo and information about our services. Pictures of pets. Our contact info. PLEASE NOTE: this is a 2 sided brochure. Please submit both inside and outside.
Should not have
• puppies, kittens - anything off message

```html
<!DOCTYPE html>
<html lang="en">
<head>
<meta charset="utf-8">
<title>Trellis Animal Respite &amp; Home Care – Inside Panel</title>
<link href="https://fonts.googleapis.com/css2?family=EB+Garamond:ital,wght@0,400;0,500;1,500;1,600&display=swap" rel="stylesheet">
<style>
:root{
  --navy:#0d1c44;
  --navy-mid:#1d3566;
  --teal:#22a99b;
  --teal-light:#6fcfc3;
  --ink:#1a1a1a;
  --white:#ffffff;
}
*{margin:0;padding:0;box-sizing:border-box}
html,body{width:1200px;height:927px;overflow:hidden;background:var(--white)}
.panel{position:relative;width:1200px;height:927px;overflow:hidden;font-family:"EB Garamond",Georgia,serif;color:var(--ink)}
.backdrop{position:absolute;inset:0}
.abs{position:absolute}
.nowrap{white-space:nowrap}
.photo-dog{left:0;top:30px;width:390px;height:257px;border:3px solid var(--white);border-left:none;
  background:linear-gradient(160deg,#e9ece9 0%,#c98a3f 45%,#a2612a 70%,#d9dcdf 100%)}
.photo-cat{left:680px;top:680px;width:520px;height:205px;
  background:linear-gradient(180deg,rgba(255,255,255,0) 0%,#b9cf9a 30%,#8fb46a 65%,#7aa55a 100%);
  -webkit-mask-image:linear-gradient(90deg,transparent 0,#000 25%);mask-image:linear-gradient(90deg,transparent 0,#000 25%)}
.title{font-style:italic;font-weight:600;font-size:29.5px;color:var(--white);left:655px;top:18px;letter-spacing:.2px}
.title .cap,.heading .cap{font-size:1.25em}
.define{color:var(--white);font-size:19px;line-height:24px;left:480px;top:62px}
.define p{padding-left:28px;text-indent:-28px;white-space:nowrap}
.define p+p{margin-top:7px}
.define em{font-weight:600}
.lead{color:var(--white);font-style:italic;font-weight:600;font-size:19px;left:480px;top:169px}
.stars{list-style:none}
.stars li{position:relative;padding-left:27px;font-size:19px;line-height:20px;margin-bottom:6.5px}
.stars li::before{content:"";position:absolute;left:0;top:1px;width:17px;height:17px;background:var(--teal);
  clip-path:polygon(50% 0,60% 40%,100% 50%,60% 60%,50% 100%,40% 60%,0 50%,40% 40%)}
.stars.on-navy li{color:var(--white);line-height:28.7px;margin-bottom:0}
.stars.on-navy li::before{top:6px;background:var(--teal-light)}
.heading{font-style:italic;font-weight:600;font-size:30px;color:var(--navy)}
.intro{left:34px;top:389px;font-style:italic;font-weight:600;font-size:19.5px;line-height:23px;color:var(--navy);white-space:nowrap}
.band{left:0;top:441px;width:790px;height:38px;padding-left:34px;
  background:linear-gradient(90deg,var(--navy) 0%,var(--navy-mid) 55%,rgba(29,53,102,0) 100%);
  color:var(--white);font-style:italic;font-weight:600;font-size:24.5px;line-height:38px;white-space:nowrap}
.approach{left:34px;top:487px;font-style:italic;font-weight:600;font-size:18.5px;line-height:23.5px;color:var(--navy);white-space:nowrap}
.services{left:34px;top:570px;width:372px}
.extras-lead{left:425px;top:551px;font-style:italic;font-weight:600;font-size:18.5px;color:var(--navy);white-space:nowrap}
.extras{left:425px;top:580px;width:300px}
.team-lead{left:810px;top:467px;font-style:italic;font-weight:600;font-size:18.5px;line-height:24px;color:var(--navy);white-space:nowrap}
.team{left:812px;top:515px;list-style:none}
.team li{position:relative;padding-left:25px;font-size:19px;line-height:26.6px;white-space:nowrap}
.team li::before{content:"";position:absolute;left:2px;top:12px;width:5px;height:5px;border-radius:50%;background:var(--ink)}
</style>
</head>
<body>
<main class="panel">
  <svg class="backdrop" width="1200" height="927" viewBox="0 0 1200 927" aria-hidden="true">
    <defs>
      <linearGradient id="sky" x1="0" y1="0" x2="0" y2="1">
        <stop offset="0" stop-color="#bfe3f1"/><stop offset=".6" stop-color="#eaf6fa"/><stop offset="1" stop-color="#ffffff"/>
      </linearGradient>
    </defs>
    <rect width="1200" height="927" fill="url(#sky)"/>
    <path d="M0 0H1200V428C1050 432 860 395 700 360C540 325 380 318 240 330C140 338 60 346 0 352Z" fill="#0d1c44"/>
    <path d="M0 352C60 346 140 338 240 330C380 318 540 325 700 360C860 395 1050 432 1200 428" fill="none" stroke="#8fa6b8" stroke-width="6"/>
    <path d="M0 360C60 354 140 346 240 338C380 326 540 333 700 368C860 403 1050 440 1200 436" fill="none" stroke="#22a99b" stroke-width="5"/>
    <path d="M0 927V895C200 878 420 870 640 876C860 882 1040 888 1200 870V927Z" fill="#22a99b"/>
    <path d="M0 895C200 878 420 870 640 876C860 882 1040 888 1200 870" fill="none" stroke="#ffffff" stroke-width="3"/>
  </svg>

  <div class="abs photo-dog" role="img" aria-label="Photo of a golden senior dog resting its head on a soft blanket"></div>

  <h1 class="abs title"><span class="cap">P</span>alliative Care and Hospice</h1>
  <div class="abs define">
    <p><em>Palliative Care</em> seeks to relieve suffering and improve quality of life at all stages<br>of illness, injury and disease, whether curable or not.</p>
    <p><em>Hospice</em> is a special kind of Palliative Care focused on those with a life expectancy<br>of less than one year.</p>
  </div>
  <p class="abs lead">Both Palliative Care and Hospice:</p>
  <ul class="abs stars on-navy" style="left:480px;top:196px">
    <li>Focus on living fully</li>
    <li>Recognize and address all suffering ~ physical, emotional, social and spiritual</li>
    <li>Use a team approach to meet the needs of the animal and his or her family</li>
    <li>Affirm life while viewing death as a natural, normal process</li>
  </ul>

  <h2 class="abs heading" style="left:130px;top:344px"><span class="cap">O</span>ur Services</h2>
  <p class="abs intro">At Trellis Animal Respite &amp; Home Care, our only goal is to support you<br>in providing the very best care for your beloved companion in your own home.</p>
  <p class="abs band">We are here for you 24 hours a day, every day of the year.</p>
  <p class="abs approach">We work as a team to address the needs of your entire family. We come with no agenda and no<br>prescribed plan, but rather follow your needs and wishes as they evolve and change over time.<br>Some of the services we offer are:</p>
  <ul class="abs stars services">
    <li>Visiting and support</li>
    <li>Administration of medication &amp; fluids</li>
    <li>Overnight and respite care</li>
    <li>Check-ins, exercise and play</li>
    <li>Assistance evaluating pain, quality of life, and<br>end of life choices</li>
    <li>Coordination of care with your vet and other<br>care professionals</li>
    <li>Home cooked meals and treats</li>
    <li>Transportation and errand running</li>
    <li>Equipment and supplies</li>
    <li>Funerals and memorials</li>
    <li>Bereavement support</li>
  </ul>

  <p class="abs extras-lead">Our skilled team members can also provide:</p>
  <ul class="abs stars extras">
    <li>Massage and Gentle Touch</li>
    <li>Cold LASER Treatments</li>
    <li>Reiki</li>
    <li>Passive Range of Motion (PROM)</li>
    <li>Rehabilitation Support</li>
    <li>Grooming</li>
    <li>Essential Oils</li>
    <li>Floral Essences</li>
    <li>Aroma Therapy</li>
    <li>Music Therapy</li>
    <li>Pet Therapy</li>
  </ul>

  <div class="abs photo-cat" role="img" aria-label="Photo of a black and white cat using a pet wheelchair on a grassy lawn"></div>

  <h2 class="abs heading" style="left:898px;top:422px"><span class="cap">O</span>ur Team</h2>
  <p class="abs team-lead">Lead by Miriam Ashby, C.T. our interdisci-<br>plinary team includes:</p>
  <ul class="abs team">
    <li>Certified Thanatologist</li>
    <li>Certified Veterinary Technicians</li>
    <li>Interfaith Spiritual Advisor</li>
    <li>Certified Small Animal Massage Therapist</li>
    <li>Animal Care Specialists</li>
    <li>Hospice Assistants</li>
    <li>Client Care Coordinator</li>
  </ul>
</main>
</body>
</html>
```